graphic showing our process of education as a process called a pipeline

Also see my updated comments on discussion section.
Title of the graphic needs to be:
TITLE = The KESIMA Strategic Leadership Pipeline = larger, bold heading
SUB-TITLE = Developing a steady flow of servant leaders for Tanzania's future = under title; smaller font
change the text for each of the 7 steps to match the outcomes listed on the newly attached PDF (strategic pipeline 11x17)
Pipe should be straight or mostly straight.
Pipe should not be in a strong or dark color.
Any icons or symbols should be simple and professional, not like cartoon or childish.
We need a graphic design that shows our PROCESS, called a "pipeline," that is creating future leaders. We are a US-based non-profit that operates a Christian school in rural Tanzania for 600 students (pre-K through 12th grade). It starts with child sponsorship program that allows poor children and orphans to attend school, we have a primary school (like USA elementary school, pre-K thru 7th), and are building a secondary boarding school (like USA middle and high school, grades 8-12), where students will live on campus in dormitories. We offer education, scholarships, leadership development experiences, help finding and securing college scholarships, academic and career counseling, placements for internships and jobs, and networking and leadership development content and events to create the next generation of servant leaders for the country. Prominent colors should probably be the green, blue and black in the Tanzania flag; we want the design to communicate "smart" and "strategic." The stages of the pipeline need to be properly named; we need to show a "leak" in the pipeline after the primary school because we currently have to send our students AWAY to other boarding schools because we don't have one. As the attached recording says, this is bad for their progress. The attached pipeline graphic is very rough and NOT meant to be imitated. It is factually correct, but is busy and not attractive.

Target Market(s)

Major financial contributors and foundations that want to give money to the cause

Industry/Entity Type

non-profit/Christian ministry in education

Font styles to use
Sans Serif

Requirements
Must have
• A "smart" and strategic" feel; preferably visible when on a half page
Nice to have
• a smart, sophisticated, serious look and feel
Should not have
• an elementary school feel

```html
<!DOCTYPE html>
<html lang="en">
<head>
<meta charset="utf-8">
<title>KESIMA Leadership Pipeline</title>
<link rel="stylesheet" href="https://fonts.googleapis.com/css2?family=Montserrat:wght@500;600;700;800&display=swap">
<style>
  :root {
    --sky: #1ea3dd;
    --card-blue: #2aa9e1;
    --coupler: #2aa9e1;
    --pipe: #b5ebf8;
    --feeder: #a7efd3;
    --badge: #3cbc3c;
    --rule: #3cbc3c;
    --ink: #1c1c1c;
    --icon: #1f1f1f;
    --paper: #ffffff;
  }
  * { box-sizing: border-box; margin: 0; padding: 0; }
  html, body { width: 1200px; height: 1200px; overflow: hidden; background: var(--paper); }
  body { position: relative; font-family: "Montserrat", Arial, sans-serif; color: var(--ink); }

  .pipeline { position: absolute; left: 0; width: 1200px; height: 470px; }
  .pipeline--current { top: 110px; }
  .pipeline--planned { top: 617px; }

  .pipeline__title {
    position: absolute; top: 20px; left: 0; width: 100%;
    text-align: center; font-size: 37px; font-weight: 800; color: var(--sky); letter-spacing: -0.2px;
  }
  .pipeline__subtitle {
    position: absolute; top: 64px; left: 0; width: 100%;
    display: flex; justify-content: center; align-items: center; gap: 16px;
    font-size: 14px; font-weight: 600; color: var(--ink); white-space: nowrap;
  }
  .pipeline__subtitle::before,
  .pipeline__subtitle::after {
    content: ""; display: block; width: 62px; height: 2px; background: var(--rule); flex: none;
  }

  .pipeline__graphic { position: absolute; left: 0; top: 0; }

  .stage {
    position: absolute; top: 122px; width: 86px; height: 133px;
    display: flex; flex-direction: column; align-items: center;
  }
  .stage__name {
    width: 100%; height: 46px; background: var(--card-blue); color: #fff;
    border-radius: 8px 8px 0 0; display: flex; align-items: center; justify-content: center;
    text-align: center; font-size: 7.5px; font-weight: 700; line-height: 1.2; padding: 8px 4px 0;
  }
  .stage__body {
    flex: 1; width: 100%; border: 1.5px dotted var(--card-blue); border-top: none;
    border-radius: 0 0 8px 8px; display: flex; flex-direction: column; align-items: center;
    padding: 2px 5px 0;
  }
  .stage__badge {
    background: var(--badge); color: #fff; font-size: 7px; font-weight: 700;
    padding: 1px 5px; border: 1px solid #fff; margin-top: -6px; letter-spacing: 0.2px;
  }
  .stage__outcome {
    margin-top: 6px; text-align: center; font-size: 7.3px; font-weight: 500; line-height: 1.3;
  }

  .icon-slot { position: absolute; background: #d9d9d9; border-radius: 4px; }
</style>
</head>
<body>

  <section class="pipeline pipeline--current" aria-label="Current pipeline with leak">
    <h1 class="pipeline__title">KESIMA Leadership Pipeline</h1>
    <p class="pipeline__subtitle">Developing a steady flow of servant leaders for Tanzania's future</p>

    <svg class="pipeline__graphic" width="1200" height="470" viewBox="0 0 1200 470">
      <g class="top-links" fill="var(--pipe)">
        <rect x="330" y="138" width="30" height="12"/><rect x="441" y="138" width="30" height="12"/>
        <rect x="552" y="138" width="30" height="12"/><rect x="662" y="138" width="30" height="12"/>
        <rect x="773" y="138" width="30" height="12"/><rect x="884" y="138" width="30" height="12"/>
      </g>
      <g class="feeders" fill="none" stroke="var(--feeder)" stroke-width="17">
        <path d="M289 256 V275 C289 300 325 290 325 318 V342"/>
        <path d="M400 256 V275 C400 300 436 290 436 318 V342"/>
        <path d="M511 256 V275 C511 300 547 290 547 318 V342"/>
        <path d="M621 256 V275 C621 300 657 290 657 318 V342"/>
        <path d="M732 256 V275 C732 300 768 290 768 318 V342"/>
        <path d="M843 256 V275 C843 300 879 290 879 318 V342"/>
        <path d="M953 256 V275 C953 300 989 290 989 318 V342"/>
      </g>
      <g class="feeder-caps" fill="var(--badge)">
        <rect x="279" y="254" width="20" height="3"/><rect x="390" y="254" width="20" height="3"/>
        <rect x="501" y="254" width="20" height="3"/><rect x="611" y="254" width="20" height="3"/>
        <rect x="722" y="254" width="20" height="3"/><rect x="833" y="254" width="20" height="3"/>
        <rect x="943" y="254" width="20" height="3"/>
      </g>
      <rect class="main-pipe" x="228" y="340" width="780" height="22" fill="var(--pipe)"/>
      <g class="couplers" fill="var(--coupler)">
        <rect x="228" y="338" width="3" height="26"/><rect x="233" y="338" width="3" height="26"/>
        <rect x="340" y="338" width="3" height="26"/><rect x="345" y="338" width="3" height="26"/>
        <rect x="451" y="338" width="3" height="26"/><rect x="456" y="338" width="3" height="26"/>
        <rect x="562" y="338" width="3" height="26"/><rect x="567" y="338" width="3" height="26"/>
        <rect x="672" y="338" width="3" height="26"/><rect x="677" y="338" width="3" height="26"/>
        <rect x="783" y="338" width="3" height="26"/><rect x="788" y="338" width="3" height="26"/>
        <rect x="894" y="338" width="3" height="26"/><rect x="899" y="338" width="3" height="26"/>
        <rect x="1003" y="338" width="3" height="26"/><rect x="1008" y="338" width="3" height="26"/>
      </g>
      <g class="drops" stroke="var(--icon)" stroke-width="1.5" stroke-dasharray="2 3">
        <line x1="399" y1="364" x2="399" y2="412"/><line x1="510" y1="364" x2="510" y2="395"/>
        <line x1="621" y1="364" x2="621" y2="395"/><line x1="731" y1="364" x2="731" y2="405"/>
        <line x1="842" y1="364" x2="842" y2="400"/>
      </g>
      <g class="leak" aria-label="Leak after primary school">
        <path d="M460 370 l-4 6 h5 l-4 7" fill="none" stroke="var(--sky)" stroke-width="2"/>
        <path d="M457 382 C457 382 450 391 450 395 a7 7 0 0 0 14 0 C464 391 457 382 457 382Z" fill="var(--sky)"/>
      </g>
      <g class="grad-cap" fill="var(--icon)">
        <polygon points="731,412 768,424 731,436 694,424"/>
        <path d="M710 430 V442 C720 450 742 450 752 442 V430 L731 437Z"/>
      </g>
    </svg>

    <div class="icon-slot" style="left:188px;top:326px;width:34px;height:36px" role="img" aria-label="Pictogram of a parent with a child"></div>
    <div class="icon-slot" style="left:1014px;top:328px;width:56px;height:34px" role="img" aria-label="Pictogram of a crowd of leaders"></div>
    <div class="icon-slot" style="left:389px;top:418px;width:20px;height:36px" role="img" aria-label="Pictogram of a child"></div>
    <div class="icon-slot" style="left:488px;top:402px;width:44px;height:44px" role="img" aria-label="Pictogram of a student with an atom symbol"></div>
    <div class="icon-slot" style="left:600px;top:403px;width:42px;height:40px" role="img" aria-label="Pictogram of a person helping another"></div>
    <div class="icon-slot" style="left:820px;top:410px;width:44px;height:36px" role="img" aria-label="Pictogram of two people shaking hands"></div>

    <div class="stage" style="left:246px"><div class="stage__name">KESIMA SPONSORSHIP PROGRAM</div><div class="stage__body"><span class="stage__badge">OUTCOME</span><p class="stage__outcome">Establishing spiritual, academic,and health foundations</p></div></div>
    <div class="stage" style="left:357px"><div class="stage__name">KESIMA PRIMARY SCHOOL</div><div class="stage__body"><span class="stage__badge">OUTCOME</span><p class="stage__outcome">Potential leaders with Biblical worldview and strong academic foundations.</p></div></div>
    <div class="stage" style="left:468px"><div class="stage__name">KESIMA SECONDARY SCHOOL</div><div class="stage__body"><span class="stage__badge">OUTCOME</span><p class="stage__outcome">Emerging leaders with concrete skills and strong servant mindset.</p></div></div>
    <div class="stage" style="left:578px"><div class="stage__name">KESIMA SERVICE LEADERSHIP EXPERIENCE</div><div class="stage__body"><span class="stage__badge">OUTCOME</span><p class="stage__outcome">Growing servant leaders with practical experience to effect change for the kingdom</p></div></div>
    <div class="stage" style="left:689px"><div class="stage__name">KESIMA HIGHER EDUCATION SUPPORT</div><div class="stage__body"><span class="stage__badge">OUTCOME</span><p class="stage__outcome">Expanding vision, capability, and motivation to solve bigger challenges for the nation.</p></div></div>
    <div class="stage" style="left:800px"><div class="stage__name">KESIMA EMPLOYMENT CENTER</div><div class="stage__body"><span class="stage__badge">OUTCOME</span><p class="stage__outcome">Capable Christ-centered leaders in the marketplace as value adding employees and entrepreneurs.</p></div></div>
    <div class="stage" style="left:910px"><div class="stage__name">KESIMA LEADERSHIP HUB</div><div class="stage__body"><span class="stage__badge">OUTCOME</span><p class="stage__outcome">Mature Christian leaders being placed and positioned for leadership roles in the community and nation.</p></div></div>
  </section>

  <section class="pipeline pipeline--planned" aria-label="Planned pipeline without leak">
    <h2 class="pipeline__title">KESIMA Leadership Pipeline</h2>
    <p class="pipeline__subtitle">Developing a steady flow of servant leaders for Tanzania's future</p>

    <svg class="pipeline__graphic" width="1200" height="470" viewBox="0 0 1200 470">
      <g class="top-links" fill="var(--pipe)">
        <rect x="330" y="138" width="30" height="12"/><rect x="441" y="138" width="30" height="12"/>
        <rect x="552" y="138" width="30" height="12"/><rect x="662" y="138" width="30" height="12"/>
        <rect x="773" y="138" width="30" height="12"/><rect x="884" y="138" width="30" height="12"/>
      </g>
      <g class="feeders" fill="none" stroke="var(--feeder)" stroke-width="17">
        <path d="M289 256 V275 C289 300 325 290 325 318 V342"/>
        <path d="M400 256 V275 C400 300 436 290 436 318 V342"/>
        <path d="M511 256 V275 C511 300 547 290 547 318 V342"/>
        <path d="M621 256 V275 C621 300 657 290 657 318 V342"/>
        <path d="M732 256 V275 C732 300 768 290 768 318 V342"/>
        <path d="M843 256 V275 C843 300 879 290 879 318 V342"/>
        <path d="M953 256 V275 C953 300 989 290 989 318 V342"/>
      </g>
      <g class="feeder-caps" fill="var(--badge)">
        <rect x="279" y="254" width="20" height="3"/><rect x="390" y="254" width="20" height="3"/>
        <rect x="501" y="254" width="20" height="3"/><rect x="611" y="254" width="20" height="3"/>
        <rect x="722" y="254" width="20" height="3"/><rect x="833" y="254" width="20" height="3"/>
        <rect x="943" y="254" width="20" height="3"/>
      </g>
      <rect class="main-pipe" x="228" y="340" width="780" height="22" fill="var(--pipe)"/>
      <g class="couplers" fill="var(--coupler)">
        <rect x="228" y="338" width="3" height="26"/><rect x="233" y="338" width="3" height="26"/>
        <rect x="340" y="338" width="3" height="26"/><rect x="345" y="338" width="3" height="26"/>
        <rect x="451" y="338" width="3" height="26"/><rect x="456" y="338" width="3" height="26"/>
        <rect x="562" y="338" width="3" height="26"/><rect x="567" y="338" width="3" height="26"/>
        <rect x="672" y="338" width="3" height="26"/><rect x="677" y="338" width="3" height="26"/>
        <rect x="783" y="338" width="3" height="26"/><rect x="788" y="338" width="3" height="26"/>
        <rect x="894" y="338" width="3" height="26"/><rect x="899" y="338" width="3" height="26"/>
        <rect x="1003" y="338" width="3" height="26"/><rect x="1008" y="338" width="3" height="26"/>
      </g>
      <g class="drops" stroke="var(--icon)" stroke-width="1.5" stroke-dasharray="2 3">
        <line x1="399" y1="364" x2="399" y2="412"/><line x1="510" y1="364" x2="510" y2="395"/>
        <line x1="621" y1="364" x2="621" y2="395"/><line x1="731" y1="364" x2="731" y2="405"/>
        <line x1="842" y1="364" x2="842" y2="400"/>
      </g>
      <g class="grad-cap" fill="var(--icon)">
        <polygon points="731,412 768,424 731,436 694,424"/>
        <path d="M710 430 V442 C720 450 742 450 752 442 V430 L731 437Z"/>
      </g>
    </svg>

    <div class="icon-slot" style="left:188px;top:326px;width:34px;height:36px" role="img" aria-label="Pictogram of a parent with a child"></div>
    <div class="icon-slot" style="left:1014px;top:328px;width:56px;height:34px" role="img" aria-label="Pictogram of a crowd of leaders"></div>
    <div class="icon-slot" style="left:389px;top:418px;width:20px;height:36px" role="img" aria-label="Pictogram of a child"></div>
    <div class="icon-slot" style="left:488px;top:402px;width:44px;height:44px" role="img" aria-label="Pictogram of a student with an atom symbol"></div>
    <div class="icon-slot" style="left:600px;top:403px;width:42px;height:40px" role="img" aria-label="Pictogram of a person helping another"></div>
    <div class="icon-slot" style="left:820px;top:410px;width:44px;height:36px" role="img" aria-label="Pictogram of two people shaking hands"></div>

    <div class="stage" style="left:246px"><div class="stage__name">KESIMA SPONSORSHIP PROGRAM</div><div class="stage__body"><span class="stage__badge">OUTCOME</span><p class="stage__outcome">Establishing spiritual, academic,and health foundations</p></div></div>
    <div class="stage" style="left:357px"><div class="stage__name">KESIMA PRIMARY SCHOOL</div><div class="stage__body"><span class="stage__badge">OUTCOME</span><p class="stage__outcome">Potential leaders with Biblical worldview and strong academic foundations.</p></div></div>
    <div class="stage" style="left:468px"><div class="stage__name">KESIMA SECONDARY SCHOOL</div><div class="stage__body"><span class="stage__badge">OUTCOME</span><p class="stage__outcome">Emerging leaders with concrete skills and strong servant mindset.</p></div></div>
    <div class="stage" style="left:578px"><div class="stage__name">KESIMA SERVICE LEADERSHIP EXPERIENCE</div><div class="stage__body"><span class="stage__badge">OUTCOME</span><p class="stage__outcome">Growing servant leaders with practical experience to effect change for the kingdom</p></div></div>
    <div class="stage" style="left:689px"><div class="stage__name">KESIMA HIGHER EDUCATION SUPPORT</div><div class="stage__body"><span class="stage__badge">OUTCOME</span><p class="stage__outcome">Expanding vision, capability, and motivation to solve bigger challenges for the nation.</p></div></div>
    <div class="stage" style="left:800px"><div class="stage__name">KESIMA EMPLOYMENT CENTER</div><div class="stage__body"><span class="stage__badge">OUTCOME</span><p class="stage__outcome">Capable Christ-centered leaders in the marketplace as value adding employees and entrepreneurs.</p></div></div>
    <div class="stage" style="left:910px"><div class="stage__name">KESIMA LEADERSHIP HUB</div><div class="stage__body"><span class="stage__badge">OUTCOME</span><p class="stage__outcome">Mature Christian leaders being placed and positioned for leadership roles in the community and nation.</p></div></div>
  </section>

</body>
</html>
```